square mobile website

Hello. Pray all is well. Peace be with you.

looking to make a website with pages information from https://veradilo.us. English and Spanish.

the header of quarnetel.com when in mobile version

clean vector images and layout of fendlecell.com

and the clean simple black and white look of tavesport.com

please use the attached logo for color guidance

also need the my account section for users to be designed

there should also be a countdown timer for days:hours:seconds on the home page

please do website in figma

```html
<!DOCTYPE html>
<html lang="en">
<head>
<meta charset="utf-8">
<title>kelvanmobile</title>
<link href="https://fonts.googleapis.com/css2?family=Chakra+Petch:wght@400;500;600;700&family=Roboto:wght@400;500;700&display=swap" rel="stylesheet">
<style>
:root{
  --lime:#c6f70a;
  --lime-soft:#f1fccc;
  --black:#000;
  --ink:#111;
  --grey:#555;
  --navy:#0d3776;
  --slate:#2c4068;
  --footer:#0c1018;
  --bar:#0d3a8c;
  --white:#fff;
}
*{margin:0;padding:0;box-sizing:border-box}
ul{list-style:none}
html,body{width:1200px;height:4699px;overflow:hidden}
body{position:relative;font-family:"Roboto",Arial,sans-serif;color:var(--ink);background:var(--white)}
.abs{position:absolute}
.display{font-family:"Chakra Petch",Arial,sans-serif;font-weight:500}
.rule{position:absolute;height:5px;width:120px;background:var(--lime);clip-path:polygon(0 0,100% 0,96% 100%,0 100%)}
.btn{position:absolute;display:flex;align-items:center;justify-content:center;font-size:13px;font-weight:500}
.btn-lime{background:var(--lime);color:#000}
.btn-black{background:#000;color:#fff}
.placeholder{position:absolute}

/* header */
.site-header{position:absolute;left:0;top:0;width:1200px;height:120px;background:var(--black)}
.brand{position:absolute;display:flex;flex-direction:column;align-items:center;color:#fff;font-family:"Roboto",sans-serif;font-weight:500}
.brand .mark{border:3px solid #fff}
.nav a{position:absolute;top:50px;color:#fff;font-size:14px;text-decoration:none;white-space:nowrap}
.account{left:945px;top:38px;width:144px;height:44px}

/* hero */
.hero{position:absolute;left:0;top:120px;width:1200px;height:494px;background:radial-gradient(ellipse at 50% 40%,#2a2a2e 0%,#141416 55%,#060607 100%)}
.hero h1{position:absolute;left:0;width:1200px;text-align:center;color:#fff;font-size:46px;top:150px}
.hero .big{position:absolute;left:0;width:1200px;text-align:center;color:var(--lime);font-size:62px;font-weight:700;top:206px}
.hero p{position:absolute;left:0;width:1200px;text-align:center;color:#fff;font-size:14px;top:290px}
.count{position:absolute;top:335px;width:76px;height:76px;background:#fff;border:2px solid #000;display:flex;align-items:center;justify-content:center;font-family:"Chakra Petch",sans-serif;font-size:32px;color:#111}
.count-label{position:absolute;top:428px;width:76px;text-align:center;color:#fff;font-size:12px}

/* generic text blocks */
.sec-title{position:absolute;font-size:37px;line-height:1.28}
.body-copy{position:absolute;font-size:14px;line-height:2.05}

/* steps */
.step{position:absolute;top:3018px;width:234px;height:298px;border:1px solid #d5d5d5;background:#fff;text-align:center}
.step.active{background:var(--lime);border-color:var(--lime)}
.step .icon{position:absolute;left:74px;top:34px;width:86px;height:86px;border-radius:50%;background:var(--navy);display:flex;align-items:center;justify-content:center}
.step h3{position:absolute;left:16px;right:16px;top:146px;font-family:"Chakra Petch",sans-serif;font-weight:500;font-size:19px;line-height:1.4}
.step p{position:absolute;left:18px;right:18px;top:212px;font-size:11px;line-height:2.1;color:#555}
.step a{position:absolute;left:0;right:0;top:212px;font-size:12px;color:var(--navy);font-weight:700;text-decoration:underline}

/* care */
.care{position:absolute;left:111px;top:3422px;width:976px;height:556px;background:var(--lime-soft)}
.checks{position:absolute;left:56px;top:0;width:700px;height:360px}
.checks li{position:absolute;left:0;width:700px;font-size:14px;color:#333;display:flex;align-items:center;gap:14px;white-space:nowrap}
.checks svg{flex:none}
.review{position:absolute;top:3834px;width:406px;height:252px;background:#fff;border:2px solid #e2f8a0;box-shadow:0 0 0 1px #eaf9b8}
.review .who{position:absolute;left:38px;top:30px;font-size:14px;color:var(--navy);line-height:1.6}
.review p{position:absolute;left:38px;right:34px;top:84px;font-size:12px;line-height:2.1;color:#555}
.review .stars{position:absolute;left:38px;top:208px;color:#f27a0c;font-size:13px;letter-spacing:1px}
.arrow{position:absolute;left:238px;width:38px;height:36px;background:var(--navy);display:flex;align-items:center;justify-content:center}

/* footer */
.footer{position:absolute;left:0;top:4195px;width:1200px;height:445px;background:var(--footer)}
.col h4{position:absolute;font-family:"Chakra Petch",sans-serif;font-weight:500;font-size:25px;color:var(--lime);white-space:nowrap}
.col li{position:absolute;font-size:14px;color:#fff;white-space:nowrap}
.legal{position:absolute;left:0;top:4640px;width:1200px;height:59px;background:var(--bar)}
.legal a{position:absolute;top:20px;color:#fff;font-size:14px;text-decoration:none;white-space:nowrap}
.legal a::before{content:"•";margin-right:12px}
</style>
</head>
<body>

<header class="site-header">
  <div class="brand" style="left:108px;top:22px;width:120px">
    <div class="mark" style="width:42px;height:42px"></div>
    <div style="font-size:17px;margin-top:6px">kelvanmobile</div>
  </div>
  <nav class="nav">
    <a style="left:283px">Phones</a>
    <a style="left:376px">Bring Your Own Phone</a>
    <a style="left:572px">Plans</a>
    <a style="left:651px">Deals</a>
    <a style="left:730px">Network</a>
    <a style="left:868px">
      <svg width="13" height="13" viewBox="0 0 14 14" style="vertical-align:-2px;margin-right:4px"><circle cx="7" cy="7" r="6" fill="none" stroke="#fff" stroke-width="1.5"/><path d="M1 7h12M7 1c-3 3-3 9 0 12M7 1c3 3 3 9 0 12" fill="none" stroke="#fff" stroke-width="1.2"/></svg>US ⌄</a>
  </nav>
  <div class="btn btn-lime account">My Account</div>
</header>

<section class="hero" role="img" aria-label="Dark blurred photo of a person holding a phone with app screens">
  <div class="abs" style="left:556px;top:52px;width:88px;height:88px;background:#fff;border:4px solid #000;outline:2px solid #fff"></div>
  <h1 class="display">Connect to the future with our</h1>
  <div class="big display">5G NETWORKS</div>
  <p>Discover our ultra-fast data plans and stylish phones that will make you feel like a star.</p>
  <div class="count" style="left:468px">08</div>
  <div class="count" style="left:562px">02</div>
  <div class="count" style="left:657px">45</div>
  <div class="count-label" style="left:468px">Days</div>
  <div class="count-label" style="left:562px">Hours</div>
  <div class="count-label" style="left:657px">Seconds</div>
</section>

<section class="intro">
  <div class="placeholder" role="img" aria-label="Phone showing the brand on a desk beside stacked boxes" style="left:111px;top:708px;width:489px;height:430px;background:linear-gradient(135deg,#3c4a66 0%,#1a1f2c 55%,#5a3a22 100%)"></div>
  <h2 class="sec-title display" style="left:672px;top:728px">Ready to conquer your<br>digital world?</h2>
  <div class="rule" style="left:672px;top:846px"></div>
  <p class="body-copy" style="left:672px;top:876px;width:415px;font-size:13px;color:#555;line-height:2.1;text-align:justify">Sed ut perspiciatis unde omnis iste natus error sit voluptatem accusantium doloremque laudantium, totam rem aperiam, eaque ipsa quae ab illo inventore</p>
  <p class="body-copy" style="left:672px;top:976px;width:415px;font-size:13px;color:#555;line-height:2.1">Veritatis et quasi architecto beatae vitae dicta sunt explicabo. Nemo enim ipsam voluptatem</p>
  <div class="btn btn-black" style="left:672px;top:1066px;width:131px;height:40px">Explore More</div>
</section>

<section class="offer" role="img" aria-label="Blue glowing particle wave over a city at night" style="position:absolute;left:0;top:1235px;width:1200px;height:455px;background:linear-gradient(180deg,#0b2a6a 0%,#0a3a8a 45%,#1565b8 70%,#06204c 100%)">
  <h2 class="sec-title display" style="left:0;width:1200px;text-align:center;top:54px;color:#fff">Get 2 plans for the price of 1</h2>
  <div class="rule" style="left:540px;top:118px"></div>
  <p class="abs" style="left:0;width:1200px;text-align:center;top:140px;color:#fff;font-size:15px">Quis autem vel eum iure reprehenderit qui in ea volupt</p>
  <div class="btn btn-lime" style="left:534px;top:178px;width:132px;height:40px">Explore More</div>
</section>

<section class="check" style="position:absolute;left:0;top:1690px;width:1200px;height:600px;background:#000">
  <h2 class="sec-title display" style="left:111px;top:134px;color:#fff">Check everything you<br>need</h2>
  <div class="rule" style="left:111px;top:253px"></div>
  <p class="body-copy" style="left:111px;top:284px;width:395px;color:#fff">Nemo enim ipsam voluptatem quia voluptas sit aspernatur aut odit aut fugit, sed quia consequuntur magni dolores eos qui ratione</p>
  <div class="btn btn-lime" style="left:111px;top:410px;width:131px;height:43px">Explore More</div>
  <div class="placeholder" role="img" aria-label="Two blue smartphones, back and front view" style="left:594px;top:60px;width:416px;height:486px;background:linear-gradient(90deg,#1d2c44 0%,#4a6690 40%,#101a36 52%,#2236a8 75%,#0b1240 100%);border-radius:40px"></div>
</section>

<section class="benefits" style="position:absolute;left:0;top:2290px;width:1200px;height:543px;background:var(--slate)">
  <div class="placeholder" role="img" aria-label="Exploded view of a smartphone with glowing circuit board" style="left:0;top:0;width:600px;height:543px;background:radial-gradient(ellipse at 45% 45%,#2d7fd0 0%,#2a3f80 40%,#2c4068 75%)"></div>
  <h2 class="sec-title display" style="left:700px;top:84px;color:#fff">Incredible offers and<br>benefits you can't<br>miss</h2>
  <div class="rule" style="left:702px;top:250px"></div>
  <p class="body-copy" style="left:702px;top:282px;width:395px;color:#fff">Nemo enim ipsam voluptatem quia voluptas sit aspernatur aut odit aut fugit, sed quia consequuntur magni dolores eos qui ratione</p>
  <div class="btn btn-lime" style="left:702px;top:403px;width:131px;height:42px">Explore More</div>
</section>

<section class="activation">
  <h2 class="sec-title display" style="left:0;width:1200px;text-align:center;top:2904px">Easy activation process</h2>
  <div class="rule" style="left:540px;top:2970px"></div>

  <div class="step" style="left:111px">
    <div class="icon"><svg width="40" height="40" viewBox="0 0 40 40"><path d="M20 4a9 9 0 0 0-9 9c0 7 9 17 9 17s9-10 9-17a9 9 0 0 0-9-9z" fill="none" stroke="#fff" stroke-width="2.5"/><circle cx="20" cy="13" r="3.5" fill="#fff"/><ellipse cx="20" cy="33" rx="12" ry="3.5" fill="none" stroke="#fff" stroke-width="2"/></svg></div>
    <h3>Check coverage in<br>your area</h3>
    <p>Quis autem vel eum iure reprehenderit qui in ea voluptate velit esse</p>
  </div>
  <div class="step active" style="left:359px">
    <div class="icon"><svg width="40" height="40" viewBox="0 0 40 40"><rect x="12" y="4" width="16" height="32" rx="3" fill="none" stroke="#fff" stroke-width="2.5"/><line x1="17" y1="31" x2="23" y2="31" stroke="#fff" stroke-width="2"/></svg></div>
    <h3>Bring your phone or<br>get a new one</h3>
    <p>Quis autem vel eum iure reprehenderit qui in ea voluptate velit esse</p>
  </div>
  <div class="step" style="left:607px">
    <div class="icon"><svg width="40" height="40" viewBox="0 0 40 40"><rect x="9" y="4" width="18" height="30" rx="3" fill="#fff"/><path d="M19 16v-5a2 2 0 0 1 4 0v9l3-1a2 2 0 0 1 3 2l-2 12h-9l-4-9a2 2 0 0 1 3-2z" fill="#fff" stroke="#0d3776" stroke-width="1.5"/></svg></div>
    <h3>Choose the plan<br>you like best</h3>
    <p>Quis autem vel eum iure reprehenderit qui in ea voluptate velit esse</p>
  </div>
  <div class="step" style="left:855px">
    <div class="icon"><svg width="44" height="40" viewBox="0 0 44 40"><path d="M6 14l14-7 14 7v14l-14 7-14-7z" fill="#fff"/><path d="M6 14l14 7 14-7M20 21v14" stroke="#0d3776" stroke-width="1.5" fill="none"/><circle cx="33" cy="28" r="8" fill="#fff" stroke="#0d3776" stroke-width="2"/><path d="M29 28l3 3 5-5" stroke="#0d3776" stroke-width="2" fill="none"/></svg></div>
    <h3>Place your order<br>and activate your<br>plan</h3>
    <a style="top:248px">Activate Your Plan</a>
  </div>
</section>

<section class="care">
  <h2 class="sec-title display" style="left:46px;top:48px">Customer care that actually cares</h2>
  <div class="rule" style="left:46px;top:108px"></div>
  <p class="abs" style="left:46px;top:136px;width:880px;font-size:15px;line-height:2;color:#444">Ut enim ad minima veniam, quis nostrum exercitationem ullam corporis suscipit laboriosam, nisi ut aliquid ex ea commodi consequatur?</p>
  <ul class="checks">
    <li style="top:228px"><svg width="16" height="16" viewBox="0 0 16 16"><rect x="1" y="3" width="11" height="11" fill="none" stroke="#0d3776" stroke-width="1.6"/><path d="M4 8l3 3 7-8" fill="none" stroke="#0d3776" stroke-width="2"/></svg>Free 2-day shipping, seriously!</li>
    <li style="top:264px"><svg width="16" height="16" viewBox="0 0 16 16"><rect x="1" y="3" width="11" height="11" fill="none" stroke="#0d3776" stroke-width="1.6"/><path d="M4 8l3 3 7-8" fill="none" stroke="#0d3776" stroke-width="2"/></svg>No credit check, no stress</li>
    <li style="top:300px"><svg width="16" height="16" viewBox="0 0 16 16"><rect x="1" y="3" width="11" height="11" fill="none" stroke="#0d3776" stroke-width="1.6"/><path d="M4 8l3 3 7-8" fill="none" stroke="#0d3776" stroke-width="2"/></svg>5G speed at full throttle!</li>
    <li style="top:336px"><svg width="16" height="16" viewBox="0 0 16 16"><rect x="1" y="3" width="11" height="11" fill="none" stroke="#0d3776" stroke-width="1.6"/><path d="M4 8l3 3 7-8" fill="none" stroke="#0d3776" stroke-width="2"/></svg>Zero annual contracts, zero hassle!</li>
  </ul>
</section>

<div class="arrow" style="top:3916px"><svg width="10" height="12" viewBox="0 0 10 12"><path d="M7 1L2 6l5 5" stroke="#fff" stroke-width="2" fill="none"/></svg></div>
<div class="arrow" style="top:3963px"><svg width="10" height="12" viewBox="0 0 10 12"><path d="M3 1l5 5-5 5" stroke="#fff" stroke-width="2" fill="none"/></svg></div>

<article class="review" style="left:296px">
  <div class="who">Ricardo D.<br>Former Norvex customer</div>
  <p>Nemo enim ipsam voluptatem quia voluptas sit aspernatur aut odit aut fugit, sed quia consequuntur magni dolores eos qui ratione voluptatem sequi nesciunt.</p>
  <div class="stars">★★★★☆</div>
</article>
<article class="review" style="left:725px">
  <div class="who">Ricardo D.<br>Former Norvex customer</div>
  <p>Nemo enim ipsam voluptatem quia voluptas sit aspernatur aut odit aut fugit, sed quia consequuntur magni dolores eos qui ratione voluptatem sequi nesciunt.</p>
  <div class="stars">★★★★☆</div>
</article>

<footer class="footer">
  <div class="brand" style="left:108px;top:75px;width:240px">
    <div class="mark" style="width:104px;height:104px;border-width:5px"></div>
    <div style="font-size:40px;margin-top:12px">kelvanmobile</div>
  </div>
  <div class="col">
    <h4 style="left:450px;top:70px">Shop</h4>
    <ul>
      <li style="left:450px;top:122px">Phone Plans</li>
      <li style="left:450px;top:155px">Phones</li>
      <li style="left:450px;top:188px">Deals</li>
      <li style="left:450px;top:221px">Fendle Kids</li>
      <li style="left:450px;top:254px">Fendle 55+</li>
      <li style="left:450px;top:287px">Unlimited Phone Plan</li>
    </ul>
  </div>
  <div class="col">
    <h4 style="left:669px;top:70px">Service Features</h4>
    <ul>
      <li style="left:669px;top:122px">5G Coverage</li>
      <li style="left:669px;top:155px">What is 5G?</li>
      <li style="left:669px;top:188px">Family Phone Plans</li>
      <li style="left:669px;top:221px">Bring Your Own Phone</li>
      <li style="left:669px;top:254px">International Calling</li>
      <li style="left:669px;top:287px">International Roaming</li>
      <li style="left:669px;top:320px">Wi-Fi Calling</li>
      <li style="left:669px;top:353px">Mobile Hotspot</li>
      <li style="left:669px;top:386px">eSIM</li>
    </ul>
  </div>
  <div class="col">
    <h4 style="left:941px;top:70px">Support</h4>
    <ul>
      <li style="left:941px;top:122px">The Help Center</li>
      <li style="left:941px;top:155px">Order Status</li>
      <li style="left:941px;top:188px">Returns &amp; Exchanges</li>
      <li style="left:941px;top:221px">Unlock Policy</li>
      <li style="left:941px;top:254px">Phone Return Policy</li>
    </ul>
  </div>
</footer>

<nav class="legal">
  <a style="left:100px">Plan Terms &amp; Conditions</a>
  <a style="left:322px">Privacy Policy</a>
  <a style="left:468px">Return Policy</a>
  <a style="left:614px">Acceptable Use Policy</a>
  <a style="left:823px">Accessibility</a>
  <a style="left:960px">Site Terms of Use</a>
</nav>

</body>
</html>
```